Business Card Design Project

We need a new fresh business card for our business. There are multiple services we offer and we need a fresh corporate card that represents us better. We start from cleaning carpet and tiles, to upholstery and curtains, to completely clean all contents and building materials after a fire, or completely dry out a home or business after a major or minor flood event. We are open to all concepts as we want to create a new look, maybe even logo, signage, vehicle signage, uniforms.
We are open to new colours etc.

Go to www.brolvaquincare.com.au for current logo and all other past ideas

Target Market(s)

Everyone is our possible client but we are targeting more coorporate

Industry/Entity Type

Building

```html
<!DOCTYPE html>
<html lang="en">
<head>
<meta charset="utf-8">
<title>Brolvaquin Care – Business Card</title>
<link rel="stylesheet" href="https://fonts.googleapis.com/css2?family=Exo+2:wght@400;500;600&display=swap">
<style>
  :root {
    --backdrop: #e6e7ea;
    --card: #ffffff;
    --card-shade: #eeeff1;
    --brand-blue: #1a5a9c;
    --brand-pink: #e0197d;
    --ink: #2b2b2b;
    --ink-soft: #4a4a4a;
  }
  * { box-sizing: border-box; margin: 0; padding: 0; }
  html, body {
    width: 1200px; height: 900px; overflow: hidden;
    background: var(--backdrop);
    font-family: "Exo 2", sans-serif;
  }
  .canvas {
    width: 1200px; height: 900px;
    display: flex; align-items: center; justify-content: center;
  }
  .business-card {
    position: relative;
    width: 1050px; height: 600px;
    border-radius: 56px;
    overflow: hidden;
    background: radial-gradient(ellipse at 55% 35%, var(--card) 40%, var(--card-shade) 100%);
    box-shadow: 0 14px 40px rgba(0,0,0,0.15);
  }
  .wave-bands { position: absolute; inset: 0; width: 100%; height: 100%; }
  .brand {
    position: absolute; left: 90px; top: 290px;
    display: flex; align-items: center; gap: 18px;
  }
  .brand-dot {
    width: 64px; height: 64px; border-radius: 50%;
    background: var(--brand-blue);
  }
  .brand-name {
    font-size: 44px; font-weight: 600; color: var(--brand-blue);
    letter-spacing: 0.5px; white-space: nowrap;
  }
  .contact-block {
    position: absolute; right: 60px; top: 40px;
    text-align: right; color: var(--ink);
  }
  .person-name {
    font-size: 32px; font-weight: 500; color: var(--brand-blue);
    letter-spacing: 2px; text-transform: uppercase; line-height: 1.2;
  }
  .person-role { font-size: 20px; color: var(--ink-soft); margin-top: 2px; }
  .address { font-size: 20px; line-height: 1.3; margin-top: 26px; color: var(--ink-soft); letter-spacing: 1px; }
  .contact-list { list-style: none; margin-top: 22px; }
  .contact-item {
    display: flex; justify-content: flex-end; align-items: center; gap: 12px;
    font-size: 16px; line-height: 28px; color: var(--ink); letter-spacing: 1.5px;
    white-space: nowrap;
  }
  .contact-icon { width: 18px; height: 18px; fill: var(--brand-blue); flex: none; }
</style>
</head>
<body>
<main class="canvas">
  <section class="business-card">
    <svg class="wave-bands" viewBox="0 0 1050 600" preserveAspectRatio="none" aria-hidden="true">
      <path d="M0,470 C220,415 480,445 700,445 C860,445 980,420 1050,385 L1050,600 L0,600 Z" fill="var(--brand-blue)"/>
      <path d="M0,530 C260,495 520,500 740,480 C900,465 1000,440 1050,420 L1050,600 L0,600 Z" fill="#ffffff"/>
      <path d="M0,543 C260,508 520,513 745,493 C905,478 1005,453 1050,434 L1050,600 L0,600 Z" fill="var(--brand-pink)"/>
    </svg>

    <div class="brand">
      <span class="brand-dot"></span>
      <span class="brand-name">Brolvaquin Care</span>
    </div>

    <div class="contact-block">
      <h1 class="person-name">Marcus Delaney</h1>
      <p class="person-role">Managing Director</p>
      <p class="address">Level 12, Harbour<br>Quay Road NSW</p>
      <ul class="contact-list">
        <li class="contact-item"><span>021 487 3952</span>
          <svg class="contact-icon" viewBox="0 0 24 24"><path d="M6.6 10.8a15 15 0 0 0 6.6 6.6l2.2-2.2a1 1 0 0 1 1-.25 11.4 11.4 0 0 0 3.6.6 1 1 0 0 1 1 1V20a1 1 0 0 1-1 1A17 17 0 0 1 3 4a1 1 0 0 1 1-1h3.5a1 1 0 0 1 1 1c0 1.25.2 2.45.6 3.6a1 1 0 0 1-.25 1z"/></svg>
        </li>
        <li class="contact-item"><span>021 487 3953</span>
          <svg class="contact-icon" viewBox="0 0 24 24"><path d="M7 1h10a2 2 0 0 1 2 2v18a2 2 0 0 1-2 2H7a2 2 0 0 1-2-2V3a2 2 0 0 1 2-2zm0 3v14h10V4zm5 15.5a1 1 0 1 0 0 2 1 1 0 0 0 0-2z"/></svg>
        </li>
        <li class="contact-item"><span>021 487 3954</span>
          <svg class="contact-icon" viewBox="0 0 24 24"><path d="M4 8h16v13H4zM7 3h10v4H7zm0 8v2h4v-2zm6 0v2h4v-2zm-6 4v2h4v-2zm6 0v2h4v-2z"/></svg>
        </li>
        <li class="contact-item"><span>hello@brolvaquincare.com.au</span>
          <svg class="contact-icon" viewBox="0 0 24 24"><rect x="2" y="5" width="20" height="14" rx="1.5"/><path d="M3 6.5l9 6.5 9-6.5" fill="none" stroke="#ffffff" stroke-width="1.8"/></svg>
        </li>
        <li class="contact-item"><span>www.brolvaquincare.com.au</span>
          <svg class="contact-icon" viewBox="0 0 24 24"><path d="M12 2a10 10 0 1 0 0 20 10 10 0 0 0 0-20zm6.9 6h-3a15 15 0 0 0-1.3-3.9A8 8 0 0 1 18.9 8zM12 4c.8 1.1 1.5 2.5 1.9 4h-3.8c.4-1.5 1.1-2.9 1.9-4zM4.3 14a8 8 0 0 1 0-4h3.4a16 16 0 0 0 0 4zm.8 2h3a15 15 0 0 0 1.3 3.9A8 8 0 0 1 5.1 16zm3-8h-3a8 8 0 0 1 4.3-3.9A15 15 0 0 0 8.1 8zM12 20c-.8-1.1-1.5-2.5-1.9-4h3.8c-.4 1.5-1.1 2.9-1.9 4zm2.3-6H9.7a14 14 0 0 1 0-4h4.6a14 14 0 0 1 0 4zm.3 5.9a15 15 0 0 0 1.3-3.9h3a8 8 0 0 1-4.3 3.9zm1.7-5.9a16 16 0 0 0 0-4h3.4a8 8 0 0 1 0 4z"/></svg>
        </li>
      </ul>
    </div>
  </section>
</main>
</body>
</html>
```